HearthMile business card and stationary design

We are looking for a simple yet elegant design for our mortgage company business card and stationary.

The card should include:
Name (Marcus Pell)
Title (CEO)
Phone Number (732-555-0182)
Address (48 Birchwell Court, Suite 314, Fernhollow, NJ 08199)
Email (email@hearthmile.example)
"NMLS" i.e. (NMLS 61947)
"Company NMLS" (Company NMLS 274615)

Contact Information for Business Card

See above

```html
<!DOCTYPE html>
<html lang="en">
<head>
<meta charset="utf-8">
<title>HearthMile Business Card</title>
<link href="https://fonts.googleapis.com/css2?family=Roboto:wght@400;500;700&display=swap" rel="stylesheet">
<style>
  :root {
    --backdrop: #cdcdcd;
    --navy: #1b2633;
    --blue: #0fb0ee;
    --white: #ffffff;
    --text-light: #f2f4f6;
  }
  * { margin: 0; padding: 0; box-sizing: border-box; }
  html, body {
    width: 1200px; height: 1200px; overflow: hidden;
    background: var(--backdrop);
    font-family: 'Roboto', Arial, sans-serif;
  }
  .sheet { position: relative; width: 1200px; height: 1200px; }
  .card {
    position: absolute; left: 150px; width: 900px; height: 514px;
    overflow: hidden;
  }
  .card--front { top: 56px; background: var(--white); }
  .card--back { top: 630px; background: var(--navy); }

  /* Front */
  .contact-panel {
    position: absolute; left: 0; top: 0; width: 388px; height: 100%;
    background: var(--navy); color: var(--text-light);
    padding: 102px 0 0 63px;
  }
  .contact-name {
    color: var(--blue); font-weight: 700; font-size: 29px; line-height: 1.1;
  }
  .contact-title {
    font-weight: 500; font-size: 19px; line-height: 1.2; margin-top: 2px;
  }
  .contact-address {
    font-size: 20px; line-height: 25px; margin-top: 22px; font-style: normal;
  }
  .contact-lines { list-style: none; margin-top: 12px; }
  .contact-lines li {
    display: flex; align-items: center; font-size: 20px; line-height: 25.5px;
  }
  .contact-lines svg { width: 16px; height: 16px; margin-right: 10px; flex: none; }
  .licences { margin-top: 12px; font-size: 20px; line-height: 25px; }
  .licences .label { color: var(--blue); margin-right: 8px; }

  .brand-area {
    position: absolute; left: 388px; top: 0; right: 19px; height: 100%;
    display: flex; align-items: center; justify-content: center;
  }
  .brand-name {
    font-weight: 500; font-size: 62px; color: var(--navy);
    letter-spacing: 0.5px; margin-top: 16px;
  }
  .accent-stripe {
    position: absolute; right: 0; top: 0; width: 19px; height: 100%;
    background: var(--blue);
  }

  /* Back */
  .back-brand {
    position: absolute; right: 98px; top: 364px; text-align: left;
    color: var(--white);
  }
  .back-brand .brand-name {
    color: var(--white); font-size: 66px; margin: 0; line-height: 1;
  }
  .back-url {
    display: block; margin-top: 8px; font-size: 16px; font-weight: 500;
    letter-spacing: 6.4px; color: var(--white);
  }
</style>
</head>
<body>
<main class="sheet">

  <section class="card card--front" aria-label="Business card front">
    <div class="contact-panel">
      <h1 class="contact-name">Marcus Pell</h1>
      <p class="contact-title">CEO</p>
      <address class="contact-address">
        48 Birchwell Court<br>
        Suite 314<br>
        Fernhollow, NJ 08199
      </address>
      <ul class="contact-lines">
        <li>
          <svg viewBox="0 0 16 16" aria-hidden="true"><path fill="#0fb0ee" d="M3.6 1.2l2.3 2.6-1.2 1.8c.9 2 2.4 3.6 4.4 4.6l1.8-1.2 2.6 2.3-1.4 2.3C7 13.4 2.6 9 2.2 3z"/></svg>
          732-555-0182
        </li>
        <li>
          <svg viewBox="0 0 16 16" aria-hidden="true"><rect x="1.5" y="3.5" width="13" height="9" rx="1" fill="#0fb0ee"/><path d="M2 4.5l6 4.2 6-4.2" fill="none" stroke="#1b2633" stroke-width="1.3"/></svg>
          info@hearthmile.example
        </li>
        <li>
          <svg viewBox="0 0 16 16" aria-hidden="true"><circle cx="8" cy="8" r="6.5" fill="#0fb0ee"/><path d="M4 5.5c1.5 0 2 1.2 3.3 1.2.8 1.2-.4 2.4.3 3.8L6.8 13M10 3c-.3 1.3.6 1.9 1.8 1.9M10.8 8.4c.8.4 1.6 1.2 1.4 2.4" fill="none" stroke="#1b2633" stroke-width="1.2"/></svg>
          hearthmile.example
        </li>
      </ul>
      <div class="licences">
        <p><span class="label">NMLS</span>61947</p>
        <p><span class="label">Company NMLS</span>274615</p>
      </div>
    </div>
    <div class="brand-area">
      <span class="brand-name">HearthMile</span>
    </div>
    <div class="accent-stripe"></div>
  </section>

  <section class="card card--back" aria-label="Business card back">
    <div class="back-brand">
      <span class="brand-name">HearthMile</span>
      <span class="back-url">www.HearthMile.example</span>
    </div>
  </section>

</main>
</body>
</html>
```